Property Portal needs Chatterloop Cover Image and Sponsor Ad Design

WHO WE ARE
Hi Pitchers! We are an advertising portal that focus on presenting the latest property launches in Singapore. Our platform and interface will provide consumer an enjoyable and easy browsing experience looking for their ideal property to buy/invest, while ensuring updated information, images/videos, and other useful description is provided on each project.

WHAT WE NEED
Our website is www.brightkeyhomes.sg, and we need designs for our Chatterloop page www.facebook.com/brightkeyhomes. One as the Cover Image (815 x 315), and one as our Sponsor Ad Image (1200 x 627). The 2 designs can be similar or different.

DESIGN
We want to convey a professional and sociable feel. A "cool" and elegant design may be suitable, although feel free to have your own look & feel as long as it suits our purpose. Try to have a focus, and not look messy. We don't want to look cheap, spammy or boring in any sense. Be creative and purposeful =) You may use the snapvault images attached or you can use your own. Add symbols or graphics if it helps to give the design a better feel.

For your reference, I find there is a number of good designs with nice look & feel in this project including those withdraw/eliminated.
http://chatterloop.pitchmart.example/contest.aspx?id=218907&page=2
http://chatterloop.pitchmart.example/contest.aspx?id=218907

IDEAS
You may want to embed our portal in an SLATEX device as part of the design (see samples below but replace callpod with SlateX). And/or you can have a blur-out image background to have a focus on what you want to show. Please note that we are not restricting any other designs concept, this is just an idea I have.

CAPTIONS
You may use one or a few of the sample captions below.
- Singapore Latest Property Launches In One Portal (slight emphasis on "in one portal")
- Latest Projects • Updated Info • Best Pricing
- Residential • Commercial • Overseas (perhaps label on images)

Hope we can find an ideal design here. We will request from pitchmart to increase the project budget to give out more participation payments if there is a few good ones. We are also looking to find suitable designers for our future projects as we need a few more designs. If you have questions, feel free to ask me and I will reply promptly.

Reason: Project cancelled and relaunch with different purpose, moved from Newsletter to Chatterloop Design.

IDEAS (UPDATED) I am thinking one way to showcase our portal is perhaps to have our website embedded in an slatex and/or notebook pro device as part of the design. I've attached some designs I came across to show what I mean (only the embedding part). If you are going to do it this way, you can use our main page www.brightkeyhomes.sg and/or a project page www.brightkeyhomes.sg/willowcrest-at-ambergate to display

Target Market(s)

Real Estate Agents, Investors, Developers, General public age 30 & above

Industry/Entity Type

Advertising

Colors
9ccb3b
00a98f
0592cd
3176b5
ffcf3e
5c5c5c

Requirements
Should not have
• I prefer not to use real people stock images unless you are very sure it will work out well.

```html
<!DOCTYPE html>
<html lang="en">
<head>
<meta charset="utf-8">
<title>Brightkeyhomes Cover</title>
<link rel="stylesheet" href="https://fonts.googleapis.com/css2?family=Montserrat:wght@300;400;600;700;800&display=swap">
<style>
  :root {
    --brand-green: #66ad46;
    --brand-green-dark: #4f9535;
    --sky-blue: #8cc3e6;
    --sky-deep: #3f86c2;
    --dusk-blue: #5d86b0;
    --lawn-green: #7aa650;
    --device-black: #16181b;
    --device-edge: #4a4d52;
    --screen-bg: #f4f6f3;
    --card-bg: #ffffff;
    --line-grey: #c9cdc8;
    --text-grey: #5c5c5c;
    --ink-white: #ffffff;
    --page-bg: #ffffff;
  }
  * { margin: 0; padding: 0; box-sizing: border-box; }
  html, body { width: 1200px; height: 444px; overflow: hidden; background: var(--page-bg); }
  .cover {
    position: relative; width: 1200px; height: 444px; overflow: hidden;
    background: var(--page-bg);
    font-family: "Montserrat", Arial, sans-serif;
  }
  .headline-panel {
    position: absolute; left: 0; top: 0; width: 690px; height: 216px;
    background: var(--brand-green); color: var(--ink-white);
    text-align: center;
  }
  .headline-panel .lead {
    position: absolute; left: 0; width: 690px; top: 22px;
    font-weight: 300; font-size: 40px; line-height: 47px; letter-spacing: 2px;
    text-transform: uppercase;
  }
  .headline-panel .emphasis {
    position: absolute; left: 0; width: 690px; top: 118px;
    font-weight: 800; font-size: 38px; line-height: 46px; letter-spacing: 2.5px;
  }
  .headline-panel .pillars {
    position: absolute; left: 0; width: 690px; top: 170px;
    font-size: 20px; line-height: 28px; letter-spacing: 1px; white-space: nowrap;
  }
  .pillars b { font-weight: 700; }
  .pillars span { font-weight: 400; }
  .pillars .dot { margin: 0 16px; font-weight: 700; }
  .photo { position: absolute; }
  .photo-residential {
    left: 11px; top: 227px; width: 335px; height: 198px;
    background: linear-gradient(180deg, var(--sky-deep) 0%, var(--sky-blue) 55%, var(--lawn-green) 100%);
  }
  .photo-commercial {
    left: 358px; top: 227px; width: 332px; height: 198px;
    background: linear-gradient(180deg, #2f73b4 0%, #9cc7e4 60%, #6fa0c0 100%);
  }
  .photo-tower {
    left: 702px; top: 11px; width: 498px; height: 414px;
    background: linear-gradient(180deg, #6c93c0 0%, var(--dusk-blue) 45%, #5e7f64 100%);
  }
  .slate-device { position: absolute; left: 674px; top: 73px; width: 284px; height: 371px; overflow: hidden; }
  .slate-device text { font-family: "Montserrat", Arial, sans-serif; }
  .brand-tag {
    position: absolute; left: 893px; top: 329px; width: 307px; height: 90px;
    background: var(--brand-green); border: 2px solid var(--ink-white); border-right: none;
    color: var(--ink-white);
    display: flex; flex-direction: column; justify-content: center; padding-left: 22px;
  }
  .brand-tag .brand-row { display: flex; align-items: center; gap: 9px; white-space: nowrap; }
  .brand-tag .brand-mark { width: 20px; height: 20px; border-radius: 50%; background: var(--ink-white); flex: none; }
  .brand-tag .brand-name { font-size: 22px; font-weight: 400; letter-spacing: 0.3px; }
  .brand-tag .brand-tagline { font-size: 7px; font-weight: 400; letter-spacing: 0.6px; margin-top: 5px; padding-left: 29px; white-space: nowrap; }
</style>
</head>
<body>
<main class="cover">
  <section class="headline-panel">
    <h1 class="lead">Singapore’s Latest<br>Property Launches</h1>
    <p class="emphasis">IN ONE PORTAL...</p>
    <p class="pillars"><b>LATEST</b> <span>PROJECT</span><span class="dot">•</span><b>UPDATED</b> <span>INFO</span><span class="dot">•</span><b>BEST</b> <span>PRICING</span></p>
  </section>

  <div class="photo photo-residential" role="img" aria-label="Photo of a mid-rise residential condominium with trees and blue sky"></div>
  <div class="photo photo-commercial" role="img" aria-label="Photo of a modern glass commercial building with lawn"></div>
  <div class="photo photo-tower" role="img" aria-label="Photo of a residential tower at dusk above landscaped gardens"></div>

  <svg class="slate-device" viewBox="0 0 284 371" aria-label="SlateX tablet showing the property portal">
    <rect x="0" y="0" width="284" height="420" rx="24" fill="var(--device-black)"/>
    <rect x="1.5" y="1.5" width="281" height="420" rx="23" fill="none" stroke="var(--device-edge)" stroke-width="2"/>
    <circle cx="142" cy="18" r="3" fill="#34373b"/>

    <g class="portal-screen">
      <rect x="32" y="34" width="220" height="340" fill="var(--screen-bg)"/>
      <rect x="32" y="34" width="220" height="28" fill="var(--card-bg)"/>
      <circle cx="102" cy="48" r="4" fill="var(--brand-green)"/>
      <text x="110" y="51" font-size="9" font-weight="600" fill="var(--brand-green)">brightkeyhomes.sg</text>

      <rect x="32" y="64" width="220" height="11" fill="var(--brand-green)"/>
      <text x="42" y="72" font-size="5" fill="var(--ink-white)">Home</text>
      <text x="66" y="72" font-size="5" fill="var(--ink-white)">About</text>
      <text x="92" y="72" font-size="5" fill="var(--ink-white)">Projects</text>
      <text x="126" y="72" font-size="5" fill="var(--ink-white)">Contact</text>

      <rect x="38" y="80" width="208" height="58" fill="url(#heroTone)" role="img" aria-label="Banner photo of a waterfront condominium"/>
      <text x="182" y="92" font-size="6" font-weight="700" fill="var(--text-grey)">WILLOWCREST</text>
      <rect x="38" y="132" width="208" height="6" fill="#2e8f86"/>

      <g class="listing-card">
        <rect x="38" y="146" width="70" height="104" fill="var(--card-bg)"/>
        <rect x="41" y="149" width="64" height="34" fill="#7fa9c9" role="img" aria-label="Listing photo"/>
        <text x="44" y="193" font-size="6" font-weight="600" fill="var(--brand-green-dark)">Ambergate</text>
        <rect x="44" y="199" width="56" height="2" fill="var(--line-grey)"/>
        <rect x="44" y="205" width="50" height="2" fill="var(--line-grey)"/>
        <rect x="44" y="211" width="54" height="2" fill="var(--line-grey)"/>
        <rect x="44" y="230" width="40" height="10" fill="var(--text-grey)"/>
        <text x="47" y="237" font-size="4.5" fill="var(--ink-white)">View details</text>
      </g>
      <g class="listing-card">
        <rect x="114" y="146" width="70" height="104" fill="var(--card-bg)"/>
        <rect x="117" y="149" width="64" height="34" fill="#8fae8a" role="img" aria-label="Listing photo"/>
        <text x="120" y="193" font-size="6" font-weight="600" fill="var(--brand-green-dark)">Fernvale</text>
        <rect x="120" y="199" width="56" height="2" fill="var(--line-grey)"/>
        <rect x="120" y="205" width="50" height="2" fill="var(--line-grey)"/>
        <rect x="120" y="211" width="54" height="2" fill="var(--line-grey)"/>
        <rect x="120" y="230" width="40" height="10" fill="var(--text-grey)"/>
        <text x="123" y="237" font-size="4.5" fill="var(--ink-white)">View details</text>
      </g>
      <g class="quick-search">
        <rect x="190" y="146" width="56" height="104" fill="var(--card-bg)"/>
        <text x="194" y="156" font-size="5.5" font-weight="600" fill="var(--brand-green-dark)">Quick Search</text>
        <rect x="194" y="162" width="48" height="7" fill="none" stroke="var(--line-grey)"/>
        <rect x="194" y="173" width="48" height="7" fill="none" stroke="var(--line-grey)"/>
        <rect x="194" y="184" width="48" height="7" fill="none" stroke="var(--line-grey)"/>
        <rect x="194" y="196" width="26" height="8" fill="var(--brand-green)"/>
      </g>
      <rect x="38" y="258" width="70" height="116" fill="var(--card-bg)"/>
      <rect x="41" y="261" width="64" height="34" fill="#9cb7cf"/>
      <rect x="114" y="258" width="70" height="116" fill="var(--card-bg)"/>
      <rect x="117" y="261" width="64" height="34" fill="#a7b99a"/>
      <rect x="190" y="258" width="56" height="116" fill="var(--card-bg)"/>
    </g>
    <defs>
      <linearGradient id="heroTone" x1="0" y1="0" x2="0" y2="1">
        <stop offset="0" stop-color="#bcd8ec"/>
        <stop offset="0.6" stop-color="#6e9fc4"/>
        <stop offset="1" stop-color="#4f8a8a"/>
      </linearGradient>
    </defs>
  </svg>

  <div class="brand-tag">
    <div class="brand-row"><span class="brand-mark"></span><span class="brand-name">brightkeyhomes.sg</span></div>
    <div class="brand-tagline">YOUR DAILY SOURCE FOR NEW LAUNCHES</div>
  </div>
</main>
</body>
</html>
```